BOLD & MINIMALIST DESIGN NEEDED

We want a very bold but minimalistic business card design that is impactful and utilizes both sides of the business card. Our current logo is included for your use.

We want bold fonts and good use of negative space. We don't want the logo to overpower the design.

Target Market(s)

Professionals who are building new commercial buildings.

Industry/Entity Type

Construction

Contact Information for Business Card

Name, Title, email, office phone, cell phone, website

Font styles to use
Serif
Sans Serif

Requirements
Must have
• Bold design!

```html
<!DOCTYPE html>
<html lang="en">
<head>
<meta charset="UTF-8">
<title>Ridgeline Design + Build — Business Card</title>
<link rel="stylesheet" href="https://fonts.googleapis.com/css2?family=Poppins:wght@300;400;500;600&display=swap">
<style>
  :root {
    --backdrop: #262626;
    --card: #202020;
    --card-edge: #2b2b2b;
    --white: #f2f2f2;
    --soft: #d6d6d6;
    --green: #7ab829;
    --graphic-light: #6a6a6a;
    --graphic-dark: #1a1a1a;
  }
  * { margin: 0; padding: 0; box-sizing: border-box; }
  html, body {
    width: 1200px; height: 576px; overflow: hidden;
    background: var(--backdrop);
    font-family: "Poppins", Arial, sans-serif;
  }
  .stage { position: relative; width: 1200px; height: 576px; }
  .card {
    position: absolute; top: 139px;
    width: 480px; height: 293px;
    background: linear-gradient(160deg, var(--card-edge) 0%, var(--card) 60%);
    border-radius: 8px;
    overflow: hidden;
  }
  .card--front { left: 103px; }
  .card--back { left: 597px; }

  .front-name {
    position: absolute; left: 47px; top: 120px;
    color: var(--white); font-weight: 600;
    font-size: 25px; line-height: 1.15; letter-spacing: 1.5px;
    text-transform: uppercase;
  }
  .front-graphic {
    position: absolute; left: 320px; top: 0;
    width: 160px; height: 293px;
    background: linear-gradient(90deg, var(--graphic-dark) 0%, #3a3a3a 55%, var(--graphic-light) 100%);
  }

  .holder { position: absolute; right: 31px; top: 33px; text-align: right; }
  .holder__name { color: var(--green); font-weight: 500; font-size: 21px; line-height: 1.2; }
  .holder__title { color: var(--soft); font-weight: 400; font-size: 11.5px; margin-top: 2px; }

  .back-name {
    position: absolute; left: 30px; top: 222px;
    display: flex; align-items: flex-start; gap: 8px;
    color: var(--white); font-weight: 600; font-size: 16px;
    line-height: 1.2; letter-spacing: 1px;
    text-transform: uppercase;
  }
  .back-name__mark { width: 12px; height: 12px; margin-top: 4px; background: var(--green); flex: none; }

  .contact { position: absolute; right: 32px; top: 216px; list-style: none; }
  .contact__item {
    display: flex; justify-content: flex-end; align-items: center; gap: 7px;
    color: var(--soft); font-weight: 300; font-size: 11.5px; line-height: 17px;
  }
  .contact__icon { width: 10px; height: 10px; fill: var(--green); }
</style>
</head>
<body>
<div class="stage">
  <section class="card card--front">
    <p class="front-name">Ridgeline<br>Design + Build</p>
    <div class="front-graphic" role="img" aria-label="Large brand graphic in brushed metal tones"></div>
  </section>

  <section class="card card--back">
    <div class="holder">
      <p class="holder__name">Daniel Reyes</p>
      <p class="holder__title">Director</p>
    </div>

    <div class="back-name"><span class="back-name__mark"></span><span>Ridgeline<br>Design + Build</span></div>

    <ul class="contact">
      <li class="contact__item">555-014-2290
        <svg class="contact__icon" viewBox="0 0 10 10"><path d="M1 2c0-1 1-1.5 4-1.5S9 1 9 2v1.2H7V2.3H3v.9H1z M2.2 4h5.6L9 9H1z"/></svg>
      </li>
      <li class="contact__item">daniel@ridgelinebuild.com
        <svg class="contact__icon" viewBox="0 0 10 10"><path d="M0 2h10v6H0z"/><path d="M0 2l5 3.5L10 2" fill="none" stroke="#202020" stroke-width="0.9"/></svg>
      </li>
      <li class="contact__item">www.ridgelinebuild.com
        <svg class="contact__icon" viewBox="0 0 10 10"><circle cx="5" cy="5" r="4.6"/><path d="M0.5 5h9M5 0.5v9M5 0.5c-2.4 2.5-2.4 6.5 0 9M5 0.5c2.4 2.5 2.4 6.5 0 9" fill="none" stroke="#202020" stroke-width="0.7"/></svg>
      </li>
    </ul>
  </section>
</div>
</body>
</html>
```